Clear sticker design for packaging

I need 4” diameter clear stickers designed for birthdays, thank you , teachers day and all the other special days to complete my gift packaging. They will go on the top of each tube to differentiate each gift for each occasion. Our design is on craft paper and I’ve uploaded a few examples of what we are trying to achieve. Last picture is the top of our tube where the stickers will be placed. We don’t want too much color unless for Christmas and Valentine’s Day maybe! We are working with black and gold or a mixture of both mostly

```html
<!DOCTYPE html>
<html lang="en">
<head>
<meta charset="UTF-8">
<title>Thank You Sticker</title>
<link rel="stylesheet" href="https://fonts.googleapis.com/css2?family=Great+Vibes&display=swap">
<style>
  :root {
    --backdrop: #dcdcdc;
    --gold-deep: #c0912a;
    --gold-mid: #dcb84c;
    --gold-light: #f6eea4;
    --ink: #141210;
    --rose-pink: #f2bcc4;
    --rose-peach: #f3b6a4;
    --rose-lilac: #cbbcf0;
    --leaf: #8fc9a2;
  }
  html, body {
    margin: 0;
    padding: 0;
    width: 1200px;
    height: 669px;
    overflow: hidden;
    background: var(--backdrop);
  }
  .canvas {
    position: relative;
    width: 1200px;
    height: 669px;
    display: flex;
    align-items: center;
    justify-content: center;
  }
  .sticker {
    width: 560px;
    height: 560px;
    filter: drop-shadow(0 2px 3px rgba(0,0,0,0.12));
  }
  .sticker-greeting {
    font-family: "Great Vibes", cursive;
    fill: var(--ink);
  }
</style>
</head>
<body>
<main class="canvas">
  <svg class="sticker" viewBox="0 0 560 560" xmlns="http://www.w3.org/2000/svg" aria-label="Round gold thank you sticker">
    <defs>
      <linearGradient id="gold-foil" x1="0" y1="0" x2="1" y2="0">
        <stop offset="0" stop-color="var(--gold-deep)"/>
        <stop offset="0.25" stop-color="var(--gold-mid)"/>
        <stop offset="0.55" stop-color="var(--gold-light)"/>
        <stop offset="0.8" stop-color="var(--gold-mid)"/>
        <stop offset="1" stop-color="var(--gold-deep)"/>
      </linearGradient>
      <linearGradient id="bouquet-tones" x1="0" y1="0" x2="1" y2="0">
        <stop offset="0" stop-color="var(--leaf)"/>
        <stop offset="0.2" stop-color="var(--rose-pink)"/>
        <stop offset="0.55" stop-color="var(--rose-peach)"/>
        <stop offset="0.8" stop-color="var(--rose-lilac)"/>
        <stop offset="1" stop-color="var(--leaf)"/>
      </linearGradient>
      <clipPath id="sticker-edge">
        <circle cx="280" cy="280" r="280"/>
      </clipPath>
    </defs>

    <circle class="sticker-base" cx="280" cy="280" r="280" fill="url(#gold-foil)"/>

    <g class="sticker-greeting">
      <text x="90" y="205" font-size="150">Thank</text>
      <text x="300" y="300" font-size="140">you</text>
    </g>

    <g clip-path="url(#sticker-edge)">
      <ellipse class="sticker-bouquet" cx="280" cy="430" rx="255" ry="110"
               fill="url(#bouquet-tones)" opacity="0.9"
               role="img" aria-label="Illustrated bouquet of pink, peach and lilac roses with green leaves"/>
    </g>
  </svg>
</main>
</body>
</html>
```